Bluefern Business Services needs a new interactive and interesting website

We need an interesting, professional, modern and functional company website for Bluefern Business Services - a young IT Services company based out of Chennai, India.

Bluefern Business Services is a fully owned subsidiary of Marlow Goods, one of the world's leading direct to consumer wine merchant.

We already have a registered company logo which must feature in the website.

We conceive, design, develop, test, implement and support IT solutions across the entire Marlow Goods IT landscape. For ex : We currently run about 25 e-commerce websites for Marlow Goods on ATG and Dot Net.

We would like to see our corporate colors used in the website. (Burgundy wine and wine green - source: www.bluefernbs-site.com)

We are looking at this website to communicate a fun, friendly and professionally managed company - reaching out to career seekers, prospective customers and general public.

For reference - The company name 'Bluefern' is an inspiration from the Marlow Goods lineage.

The second image with the world map is stickered on our main entrance to the office, I am not sure where this can be used -just putting it out there..

Please note that there are only a few more days to submit designs for this contest  !

I would appreciate if you can help posting your designs in time for our review and consideration.

Thanks.

Reason: Thanks for your inputs. We have a number of designers and a lot to digest and work with in the past few days. There has been a rush of new designs in the last few days Hence we will require more time to process these and make our decision. Hence i am requesting the contest to be open for more days. Regards, Tarun

Target Market(s)

Prospective job seekers who want to know more about the company and also wish to apply for a job vacancy
People wanting to know more about the company in general and our progress
People who want to see what we offer and how we can help them too - prospective customers
Companies that are interested in our IT Captive journey and are looking for a business opportunity

Industry/Entity Type

E-Commerce

Requirements
Must have
• Log In/ Register facility acting as a Single Sign on for Intranet (Employees)

Facility to post job vacancies (with an expiry date) and enable people to apply for a role and upload their CV/Resume.

Facility to Review Job applications

Facility for website visitors to contact Bluefern business Services via an online 'Contact Us' form with a split of job seekers and business opportunities

Gallery facility to upload pictures regarding company events
Nice to have
• Less Cluttered and contemporary design
Some Wine/Vineyard inspirations will be good but not too much, the company is an IT services company

```html
<!DOCTYPE html>
<html lang="en">
<head>
<meta charset="utf-8">
<title>Bluefern Business Services</title>
<link href="https://fonts.googleapis.com/css2?family=Carlito:wght@400;700&display=swap" rel="stylesheet">
<style>
:root{
  --burgundy:#8a0040;
  --heading:#8b0a3f;
  --green-top:#a9b51c;
  --green-bottom:#7d8b0c;
  --olive:#7b8a2b;
  --text:#555;
  --text-dark:#444;
  --white:#fff;
}
*{margin:0;padding:0;box-sizing:border-box}
html,body{width:997px;height:1200px;overflow:hidden;background:var(--white)}
body{position:relative;font-family:"Carlito",Calibri,Arial,sans-serif;color:var(--text)}
a{color:inherit;text-decoration:none}
.abs{position:absolute}

.top-band{left:0;top:0;width:997px;height:210px;background:var(--burgundy)}
.brand{left:108px;top:34px;display:flex;align-items:center;gap:8px;color:var(--white)}
.brand-dot{width:30px;height:30px;border-radius:50%;background:var(--white)}
.brand-name{font-size:25px;font-weight:700;line-height:1}
.brand-name small{display:block;font-size:19px;font-weight:700;margin-top:2px}
.utility-links{right:108px;top:81px;font-size:11px;color:var(--white)}

.main-nav{left:108px;top:104px;width:781px;height:50px;background:linear-gradient(var(--green-top),var(--green-bottom))}
.nav-item{top:0;height:50px;line-height:50px;color:var(--white);font-weight:700;font-size:13px}
.nav-sep{top:0;width:1px;height:50px;background:rgba(0,0,0,.12);box-shadow:1px 0 0 rgba(255,255,255,.15)}
.search{left:565px;top:16px;width:204px;height:21px;background:var(--white);border-radius:2px;font-size:7px;color:#777;line-height:21px;padding-left:7px}
.search svg{position:absolute;right:6px;top:5px}

.hero{left:108px;top:162px;width:781px;height:341px;background:linear-gradient(180deg,#e9a129 0%,#eb8a2a 35%,#c99a3c 55%,#7e8c2e 70%,#5c7a22 100%)}
.hero-dots{left:818px;top:476px;display:flex;gap:4px}
.hero-dots span{width:8px;height:8px;background:var(--white)}
.hero-dots span.active{background:var(--burgundy)}

h2{position:absolute;font-size:13px;font-weight:700;color:var(--heading)}
.welcome-text{left:108px;top:570px;width:385px;font-size:10.4px;line-height:20px}
.welcome-text p{margin-bottom:20px}

.event{width:114px}
.event-photo{position:relative;width:114px;background:linear-gradient(135deg,#d9dde3,#6f7784)}
.event-icon{position:absolute;left:0;bottom:0;width:29px;height:29px;background:var(--olive);display:flex;align-items:center;justify-content:center}
.event-caption{font-size:9px;color:var(--text-dark);margin-top:6px;margin-left:-2px}

.opps{left:108px;top:914px;width:250px;font-size:10.4px;line-height:16.6px}
.opps .post{margin-bottom:16px}
.opps strong,.see-all{font-weight:700;color:var(--text-dark)}
.services-list{left:376px;top:920px;font-size:10.6px;font-weight:700;color:var(--text-dark);line-height:19.6px;list-style:none}
.services-text{left:376px;top:1011px;width:255px;font-size:8.6px;line-height:16.6px}
.client{font-size:12px;font-weight:700;color:var(--heading);display:flex;align-items:center;gap:5px}
.client i{display:inline-block;width:10px;height:10px;border-radius:50%;background:var(--heading)}
.more-logos{left:779px;top:1009px;font-size:10.4px;font-weight:700;color:var(--text-dark)}

.footer{left:0;top:1107px;width:997px;height:93px;background:var(--burgundy);color:var(--white)}
.footer-links{left:115px;top:25px;font-size:10.6px;word-spacing:2px}
.footer-links span{margin:0 9px}
.copyright{left:115px;top:51px;font-size:10.6px}
.social{top:42px;font-size:10px;font-weight:700;display:flex;align-items:center;gap:4px}
.social i{display:inline-block;width:9px;height:9px;background:var(--white)}
</style>
</head>
<body>

<div class="abs top-band"></div>

<div class="abs brand">
  <span class="brand-dot"></span>
  <div class="brand-name">Bluefern<small>Business Services</small></div>
</div>

<div class="abs utility-links"><a href="#">Current opportunities</a> | <a href="#">Contact us</a></div>

<nav class="abs main-nav">
  <a class="abs nav-item" style="left:17px" href="#">Home</a>
  <span class="abs nav-sep" style="left:74px"></span>
  <a class="abs nav-item" style="left:92px" href="#">About us</a>
  <span class="abs nav-sep" style="left:165px"></span>
  <a class="abs nav-item" style="left:184px" href="#">Clients</a>
  <span class="abs nav-sep" style="left:238px"></span>
  <a class="abs nav-item" style="left:247px" href="#">Services</a>
  <span class="abs nav-sep" style="left:312px"></span>
  <a class="abs nav-item" style="left:334px" href="#">Careers</a>
  <span class="abs nav-sep" style="left:391px"></span>
  <a class="abs nav-item" style="left:419px" href="#">Contact us</a>
  <div class="abs search">Type search
    <svg width="11" height="11" viewBox="0 0 11 11"><circle cx="4.5" cy="4.5" r="3.3" fill="none" stroke="#999" stroke-width="1.2"/><line x1="7" y1="7" x2="10" y2="10" stroke="#999" stroke-width="1.6"/></svg>
  </div>
</nav>

<div class="abs hero" role="img" aria-label="Vineyard rows under an orange sunset sky with a bare tree in the foreground"></div>
<div class="abs hero-dots"><span class="active"></span><span></span><span></span><span></span></div>

<h2 style="left:108px;top:536px">Welcome</h2>
<div class="abs welcome-text">
  <p>Welcome to Bluefern Business Services, an emerging provider of global IT consulting and software services. We are part of the Marlow Goods group, a family run business and the world's largest multi-channel home delivery wine merchant operating in the UK, USA, Australia, Germany, Hong Kong, Poland and Switzerland.</p>
  <p>Mainly based in the rich cultural city of Chennai in the south east of India, Bluefern Business Services' vision is to deliver outstanding technology solutions to all of the Marlow Goods' group companies that improve business processes, drive efficiencies, support rapid growth and elevate the overall customer experience to a different level.</p>
  <p>For further information about Marlow Goods please visit www.marlowgoods-site.com or alternatively contact us.</p>
</div>

<h2 style="left:507px;top:536px">Events</h2>

<div class="abs event" style="left:515px;top:568px">
  <div class="event-photo" style="height:104px" role="img" aria-label="Business people shaking hands in an office">
    <span class="event-icon"><svg width="17" height="13" viewBox="0 0 17 13"><rect x="0" y="2" width="17" height="11" rx="1" fill="#fff"/><rect x="5" y="0" width="7" height="3" fill="#fff"/><circle cx="8.5" cy="7.5" r="3" fill="#7b8a2b"/></svg></span>
  </div>
  <div class="event-caption">Neque porro quisquam</div>
</div>
<div class="abs event" style="left:641px;top:568px">
  <div class="event-photo" style="height:104px;background:linear-gradient(#fff 0,#fff 11px,#7d94ad 11px,#c7cdd4 100%)" role="img" aria-label="Team meeting around a laptop">
    <span class="event-icon" style="bottom:13px"><svg width="15" height="17" viewBox="0 0 15 17"><rect x="0.75" y="0.75" width="13.5" height="15.5" fill="none" stroke="#fff" stroke-width="1.5"/><line x1="4" y1="1" x2="4" y2="16" stroke="#fff"/><line x1="11" y1="1" x2="11" y2="16" stroke="#fff"/><line x1="4" y1="8.5" x2="11" y2="8.5" stroke="#fff"/></svg></span>
  </div>
  <div class="event-caption">Neque porro quisquam</div>
</div>
<div class="abs event" style="left:766px;top:568px">
  <div class="event-photo" style="height:104px" role="img" aria-label="Presenter speaking to a seated team">
    <span class="event-icon"><svg width="17" height="13" viewBox="0 0 17 13"><rect x="0" y="2" width="17" height="11" rx="1" fill="#fff"/><rect x="5" y="0" width="7" height="3" fill="#fff"/><circle cx="8.5" cy="7.5" r="3" fill="#7b8a2b"/></svg></span>
  </div>
  <div class="event-caption">Neque porro quisquam</div>
</div>
<div class="abs event" style="left:515px;top:703px">
  <div class="event-photo" style="height:104px" role="img" aria-label="Colleagues working together at a laptop">
    <span class="event-icon"><svg width="15" height="17" viewBox="0 0 15 17"><rect x="0.75" y="0.75" width="13.5" height="15.5" fill="none" stroke="#fff" stroke-width="1.5"/><line x1="4" y1="1" x2="4" y2="16" stroke="#fff"/><line x1="11" y1="1" x2="11" y2="16" stroke="#fff"/><line x1="4" y1="8.5" x2="11" y2="8.5" stroke="#fff"/></svg></span>
  </div>
  <div class="event-caption">Neque porro quisquam</div>
</div>
<div class="abs event" style="left:641px;top:703px">
  <div class="event-photo" style="height:104px" role="img" aria-label="Team reviewing documents at a desk">
    <span class="event-icon"><svg width="17" height="13" viewBox="0 0 17 13"><rect x="0" y="2" width="17" height="11" rx="1" fill="#fff"/><rect x="5" y="0" width="7" height="3" fill="#fff"/><circle cx="8.5" cy="7.5" r="3" fill="#7b8a2b"/></svg></span>
  </div>
  <div class="event-caption">Neque porro quisquam</div>
</div>
<div class="abs event" style="left:766px;top:703px">
  <div class="event-photo" style="height:104px" role="img" aria-label="Manager pointing during a group discussion">
    <span class="event-icon"><svg width="15" height="17" viewBox="0 0 15 17"><rect x="0.75" y="0.75" width="13.5" height="15.5" fill="none" stroke="#fff" stroke-width="1.5"/><line x1="4" y1="1" x2="4" y2="16" stroke="#fff"/><line x1="11" y1="1" x2="11" y2="16" stroke="#fff"/><line x1="4" y1="8.5" x2="11" y2="8.5" stroke="#fff"/></svg></span>
  </div>
  <div class="event-caption">Neque porro quisquam</div>
</div>

<h2 style="left:108px;top:880px">Latest&nbsp; Oppurtunities</h2>
<div class="abs opps">
  <div class="post"><strong>26/11/2013</strong><br>Software Developers/Programmer Analysts - AX<br>We are looking for a AX Software Developer to join...<br>&nbsp;Read more</div>
  <div class="post"><strong>26/11/2013</strong><br>Software Developers/Programmer Analysts - ATG<br>We are looking for a ATG Software Developer to<br>join... read more</div>
  <div class="see-all">See all current opportunities</div>
</div>

<h2 style="left:376px;top:880px">Services</h2>
<ul class="abs services-list">
  <li>Packaged Applications</li>
  <li>Enterprise Application Integration</li>
  <li>Digital Commerce</li>
  <li>Application Development &amp; Maintenance</li>
</ul>
<p class="abs services-text">The services we provide enable the businesses we support to efficiently manage key functions, including order management (encompassing e-commerce websites, inbound and outbound call centre operations), order ...read more</p>

<h2 style="left:652px;top:880px">Clients</h2>
<div class="abs client" style="left:668px;top:937px"><i></i>Vermont Wines</div>
<div class="abs client" style="left:763px;top:937px"><i></i>Larchfield Wine</div>
<div class="abs client" style="left:664px;top:1009px"><i></i>Ledger Wine Club</div>
<div class="abs more-logos">For More Logos &gt;&gt;</div>

<footer class="abs footer">
  <div class="abs footer-links"><a href="#">Home</a><span>|</span><a href="#">About us</a><span>|</span><a href="#">Clients</a><span>|</span><a href="#">Services</a><span>|</span><a href="#">Careers</a><span>|</span><a href="#">Contact us</a></div>
  <div class="abs copyright">Copyright Bluefern Business Services Private Limited.</div>
  <a class="abs social" style="left:790px" href="#"><i></i>Friendbook</a>
  <a class="abs social" style="left:860px" href="#"><i></i>WorkLink</a>
</footer>

</body>
</html>
```